The Copperline Collective's website for high impact furniture promotions

I am looking for a simple website. we are a promotional company that runs events for furniture stores to increase sales for short periods of time. i would like the website to have about 4 areas to explain our company. I would like it to be simple and user friendly. I would like a link to chatterbook and a contact section. I am attaching our logo that i would like somewhere large or possibly in the backround. I am open to different color schemes. I would like to convey fast paced, modern, reliable. I am open to all different styles and look forward to seeing whats out there. we are looking for a quick turn around, so if we see one that we like quick, we will pick that one thanks
Reason: looking for some really creative designs and want to give a fair amount of time to produce
Target Market(s)
Retail Furniture store owners
Industry/Entity Type
It Company
Number of Pages Required
1 page
Colors
Designer to choose colors to be used in the design.
Look and feel

```html
<!DOCTYPE html>
<html lang="en">
<head>
<meta charset="utf-8">
<title>The Copperline Collective — High Impact Furniture Promotions</title>
<link href="https://fonts.googleapis.com/css2?family=Montserrat:wght@600;700&family=Open+Sans:wght@400;600;700&display=swap" rel="stylesheet">
<style>
:root{
  --navy:#0e1a5e;
  --navy-deep:#0a1448;
  --copper:#a8764a;
  --ink:#1c1c2a;
  --body:#444a55;
  --light:#ffffff;
  --grey-band:#e9e9ea;
  --footer:#15171c;
  --footer-text:#c9cad0;
  --card-border:#e3e3e6;
}
*{box-sizing:border-box;margin:0;padding:0}
html,body{width:1200px;height:3232px;overflow:hidden}
body{position:relative;background:var(--light);font-family:"Open Sans",Arial,sans-serif;color:var(--body)}
.abs{position:absolute}
h1,h2,h3{font-family:"Montserrat",Arial,sans-serif}

/* nav */
.nav{top:0;left:0;width:1200px;height:82px;background:var(--light);border-top:4px solid var(--navy);z-index:3}
.nav a{position:absolute;top:30px;font-size:17px;color:var(--ink);text-decoration:none;letter-spacing:.5px}
.brand-badge{top:0;left:492px;width:216px;height:196px;border-radius:0 0 108px 108px;background:var(--light);z-index:4;display:flex;flex-direction:column;align-items:center;justify-content:center;padding-top:30px}
.brand-name{font-family:"Open Sans",Arial,sans-serif;font-weight:600;color:var(--copper);font-size:19px;line-height:1.25;text-align:center;letter-spacing:2px;text-transform:uppercase}

/* hero */
.hero{top:0;left:0;width:1200px;height:595px;clip-path:polygon(0 0,100% 0,100% 565px,50% 595px,0 565px);background:linear-gradient(160deg,#4a4640 0%,#6b645a 35%,#3b3833 70%,#2c2a27 100%)}
.hero-shade{top:0;left:0;width:1200px;height:595px;clip-path:polygon(0 0,100% 0,100% 565px,50% 595px,0 565px);background:rgba(20,22,30,.35)}
.hero-title{top:240px;left:0;width:1200px;text-align:center;color:var(--light);font-size:46px;font-weight:700;letter-spacing:1px}
.hero-text{top:326px;left:260px;width:680px;text-align:center;color:var(--light);font-size:18px;font-weight:600;line-height:32px}
.btn-outline{top:416px;left:535px;width:130px;height:50px;border:2px solid var(--light);background:var(--navy);color:var(--light);font-size:17px;font-weight:600;display:flex;align-items:center;justify-content:center}
.dots{top:574px;left:548px;display:flex;gap:6px}
.dots span{width:18px;height:18px;border-radius:50%;background:#a7a5a0}
.dots span.on{background:var(--light);border:3px solid var(--navy)}

/* section titles */
.sec-title{left:0;width:1200px;text-align:center;font-size:28px;font-weight:700;color:var(--navy);letter-spacing:.5px}
.sec-rule{left:540px;width:120px;height:2px;background:var(--navy)}
.sec-rule.light{background:var(--light)}

.why-intro{top:796px;left:110px;width:980px;text-align:center;font-size:13px;line-height:26px}
.card{top:896px;width:282px;height:281px;background:var(--light);border:1px solid var(--card-border);box-shadow:0 2px 8px rgba(0,0,0,.08);text-align:center;padding-top:34px}
.card.active{background:var(--navy);border-color:var(--navy)}
.card svg{width:80px;height:80px}
.card h3{margin-top:22px;font-size:18px;color:var(--ink);font-weight:700}
.card p{margin:16px auto 0;width:236px;font-size:13px;line-height:22px;color:var(--body)}
.card.active h3,.card.active p{color:var(--light)}

/* trading */
.trading{top:1239px;left:0;width:1200px;height:603px;background:linear-gradient(180deg,#15246e 0%,#0e1a5e 55%,#0a1448 100%);clip-path:polygon(0 0,50% 47px,100% 0,100% 100%,50% 552px,0 100%)}
.trading-title{top:1355px;color:var(--light)}
.trading-text{top:1450px;left:120px;width:960px;text-align:center;color:#d5d8e6;font-size:15.5px;line-height:30px}
.trading-box{top:1552px;left:99px;width:1002px;height:161px;background:rgba(120,124,150,.35);color:var(--light);font-size:13.5px;font-weight:600;line-height:29px;text-align:center;padding:32px 30px}

/* about */
.chair{top:1896px;left:118px;width:292px;height:334px;border-radius:6px;background:linear-gradient(180deg,#5a4230 0%,#4a3524 55%,#6b3f2a 100%)}
.about-title{top:1888px;left:504px;font-size:28px;font-weight:700;color:var(--navy)}
.about-rule{top:1934px;left:504px;width:74px;height:2px;background:var(--navy)}
.about-text{top:1956px;left:504px;width:600px;font-size:14px;line-height:23px}
.checks{top:2018px;left:504px;list-style:none}
.checks li{display:flex;align-items:center;height:36px;font-size:14.5px;color:var(--ink);font-weight:600;font-family:"Open Sans",Arial,sans-serif}
.checks svg{width:20px;height:20px;margin-right:12px}

/* faq */
.faq{top:2297px;left:0;width:1200px;height:480px;background:var(--grey-band)}
.faq-title{top:2347px}
.faq-item{left:99px;width:476px;height:47px;border:2px solid var(--navy);border-radius:14px;display:flex;align-items:center;justify-content:space-between;padding:0 22px 0 18px;font-size:15px;color:var(--navy);font-weight:600;background:var(--light)}
.faq-item.open{background:var(--navy);color:var(--light)}
.answers-title{top:2452px;left:623px;font-size:21px;color:var(--navy);font-weight:600;font-family:"Open Sans",Arial,sans-serif}
.answers-list{top:2496px;left:623px;list-style:none}
.answers-list li{display:flex;align-items:center;height:27px;font-size:15px;color:var(--navy)}
.answers-list li::before{content:"";width:10px;height:10px;border:2px solid var(--navy);border-radius:50%;margin-right:12px}
.answers-text{top:2568px;left:623px;width:490px;font-size:13px;line-height:23px}

/* footer */
.footer{top:2733px;left:0;width:1200px;height:499px;background:var(--footer);clip-path:polygon(0 0,25% 22px,50% 48px,75% 22px,100% 0,100% 100%,0 100%)}
.footer-brand{top:2912px;left:98px;width:180px;text-align:center}
.footer-brand .brand-name{font-size:16px}
.f-head{top:2860px;font-family:"Open Sans",Arial,sans-serif;font-size:17px;font-weight:700;color:var(--light);letter-spacing:.5px}
.f-rule{top:2890px;width:36px;height:2px;background:var(--light)}
.f-links{top:2912px;left:340px;list-style:none}
.f-links li{height:32px;font-size:14px;color:var(--footer-text)}
.f-links li::before{content:"› ";color:var(--light)}
.f-contact{left:524px;width:250px;display:flex;gap:16px}
.f-contact .ico{width:40px;height:40px;border:2px solid var(--light);border-radius:50%;display:flex;align-items:center;justify-content:center;flex:none}
.f-contact .ico svg{width:18px;height:18px}
.f-contact b{display:block;color:var(--light);font-size:15px;margin-bottom:4px}
.f-contact span{display:block;font-size:12px;color:var(--footer-text);line-height:18px}
.field{border:1px solid #b9bcc8;border-radius:3px;font-size:11px;color:var(--footer-text);padding:6px 8px}
.btn-send{top:3033px;left:812px;width:120px;height:36px;border:2px solid #b9bcc8;background:var(--navy);color:var(--light);font-size:12px;display:flex;align-items:center;justify-content:center}
.f-line{top:3146px;left:98px;width:1004px;height:1px;background:#4a4c54}
.copyright{top:3174px;left:98px;font-size:14px;font-weight:600;color:var(--light)}
.social{top:3166px;left:1060px;display:flex;align-items:center;gap:10px;color:var(--light);font-size:13px}
.social i{width:34px;height:34px;border:2px solid var(--light);border-radius:50%;display:block}
</style>
</head>
<body>

<header class="abs nav">
  <a style="left:98px">HOME</a>
  <a style="left:222px">ABOUT US</a>
  <a style="left:377px">TRADING</a>
  <a style="left:750px">STORES</a>
  <a style="left:870px">FURNITURE</a>
  <a style="left:1022px">CONTACT</a>
</header>
<div class="abs brand-badge"><div class="brand-name">The<br>Copperline<br>Collective</div></div>

<section>
  <div class="abs hero" role="img" aria-label="Photo of a bright furnished living room with sofas, armchairs and a television"></div>
  <div class="abs hero-shade"></div>
  <h1 class="abs hero-title">COPPERLINE COLLECTIVE</h1>
  <p class="abs hero-text">We are a promotional company that runs events for furniture stores to increase sales for short periods of time.</p>
  <div class="abs btn-outline">READ MORE</div>
  <div class="abs dots"><span class="on"></span><span></span><span></span><span></span><span></span></div>
</section>

<section>
  <h2 class="abs sec-title" style="top:692px">WHY COPPERLINE COLLECTIVE</h2>
  <div class="abs sec-rule" style="top:756px"></div>
  <p class="abs why-intro">Duis aute irure dolor in reprehenderit in voluptate velit esse cillum dolore eu fugiat nulla pariatur. Excepteur sint occaecat cupidatat non proident,<br>sunt in culpa qui officiar.</p>

  <div class="abs card" style="left:123px">
    <svg viewBox="0 0 80 80" fill="none" stroke="#0e1a5e" stroke-width="4" stroke-linejoin="round"><path d="M14 34l34-16v40L14 46z" fill="#0e1a5e"/><path d="M20 46l6 18h8l-4-16"/><path d="M56 30l10-6M58 38h12M56 46l10 6"/></svg>
    <h3>Promotional Company</h3>
    <p>Nemo enim ipsam voluptatem quia voluptas sit aspernatur aut odit aut fugit, sed quia consequuntur.</p>
  </div>
  <div class="abs card active" style="left:459px">
    <svg viewBox="0 0 80 80" fill="none" stroke="#fff" stroke-width="3.5" stroke-linejoin="round"><rect x="20" y="10" width="52" height="40" rx="3"/><path d="M28 40l10-10 8 6 16-16"/><path d="M10 70V50l10-8 8 8v20"/></svg>
    <h3>Trading Services</h3>
    <p>Nemo enim ipsam voluptatem quia voluptas sit aspernatur aut odit aut fugit, sed quia consequuntur.</p>
  </div>
  <div class="abs card" style="left:793px">
    <svg viewBox="0 0 80 80" fill="#0e1a5e"><rect x="26" y="6" width="28" height="30" rx="6"/><rect x="18" y="24" width="6" height="18" rx="3"/><rect x="56" y="24" width="6" height="18" rx="3"/><rect x="22" y="40" width="36" height="8" rx="3"/><rect x="37" y="48" width="6" height="14"/><path d="M22 70l18-8 18 8" stroke="#0e1a5e" stroke-width="4" fill="none"/></svg>
    <h3>Furniture Stores</h3>
    <p>Nemo enim ipsam voluptatem quia voluptas sit aspernatur aut odit aut fugit, sed quia consequuntur.</p>
  </div>
</section>

<section>
  <div class="abs trading" role="img" aria-label="Deep blue tinted photo of a furniture showroom interior"></div>
  <h2 class="abs sec-title trading-title">OUR TRADING</h2>
  <div class="abs sec-rule light" style="top:1412px;left:560px;width:80px"></div>
  <p class="abs trading-text">Nemo enim ipsam voluptatem quia voluptas sit aspernatur aut odit aut fugit, sed quia consequuntur magni dolores eos qui ratione voluptatem sequi nesciunt.</p>
  <div class="abs trading-box">Sed ut perspiciatis unde omnis iste natus error sit voluptatem accusantium doloremque laudantium, totam rem aperiam, eaque ipsa quae ab illo inventore veritatis et quasi architecto beatae vitae dicta sunt explicabo. Nemo enim ipsam voluptatem quia voluptas sit aspernatur aut odit aut fugit, sed quia consequuntur magni dolores eos qui ratione voluptatem.</div>
</section>

<section>
  <div class="abs chair" role="img" aria-label="Photo of a brown upholstered armless chair with wooden legs"></div>
  <h2 class="abs about-title">ABOUT US</h2>
  <div class="abs about-rule"></div>
  <p class="abs about-text">Nemo enim ipsam voluptatem quia voluptas sit aspernatur aut odit aut fugit, sed quia conse quuntur magni dolores eos qui ratione voluptatem</p>
  <ul class="abs checks">
    <li><svg viewBox="0 0 20 20"><rect x="1" y="3" width="15" height="15" fill="none" stroke="#0e1a5e" stroke-width="2"/><path d="M5 10l4 4 10-12" fill="none" stroke="#0e1a5e" stroke-width="2.6"/></svg>Nemo enim ipsam voluptatem quia voluptas</li>
    <li><svg viewBox="0 0 20 20"><rect x="1" y="3" width="15" height="15" fill="none" stroke="#0e1a5e" stroke-width="2"/><path d="M5 10l4 4 10-12" fill="none" stroke="#0e1a5e" stroke-width="2.6"/></svg>Asperiatur aut odit aut fugit, sed quia consequuntur</li>
    <li><svg viewBox="0 0 20 20"><rect x="1" y="3" width="15" height="15" fill="none" stroke="#0e1a5e" stroke-width="2"/><path d="M5 10l4 4 10-12" fill="none" stroke="#0e1a5e" stroke-width="2.6"/></svg>Neque porro quisquam est, qui dolorem ipsum quia dolor sit amet</li>
    <li><svg viewBox="0 0 20 20"><rect x="1" y="3" width="15" height="15" fill="none" stroke="#0e1a5e" stroke-width="2"/><path d="M5 10l4 4 10-12" fill="none" stroke="#0e1a5e" stroke-width="2.6"/></svg>Adipisci velit, sed quia non numquam eius modi tempora</li>
    <li><svg viewBox="0 0 20 20"><rect x="1" y="3" width="15" height="15" fill="none" stroke="#0e1a5e" stroke-width="2"/><path d="M5 10l4 4 10-12" fill="none" stroke="#0e1a5e" stroke-width="2.6"/></svg>Enim ad minima veniam, quis nostrum exercitationem ullam</li>
    <li><svg viewBox="0 0 20 20"><rect x="1" y="3" width="15" height="15" fill="none" stroke="#0e1a5e" stroke-width="2"/><path d="M5 10l4 4 10-12" fill="none" stroke="#0e1a5e" stroke-width="2.6"/></svg>Quis autem vel eum iure reprehenderit qui in ea voluptate</li>
  </ul>
</section>

<section>
  <div class="abs faq"></div>
  <h2 class="abs sec-title faq-title">OUR FAQ'S</h2>
  <div class="abs sec-rule" style="top:2394px;left:560px;width:80px"></div>
  <div class="abs faq-item open" style="top:2444px">Nemo enim ipsam voluptatem quia?<span>»</span></div>
  <div class="abs faq-item" style="top:2508px">Dolores eos qui ratione voluptatem sequi?<span>»</span></div>
  <div class="abs faq-item" style="top:2569px">Architecto beatae vitae dicta sunt explicabo?<span>»</span></div>
  <div class="abs faq-item" style="top:2629px">Perspiciatis unde omnis iste natus error sit?<span>»</span></div>
  <h3 class="abs answers-title">Answers to your questions:</h3>
  <ul class="abs answers-list">
    <li>Nemo enim ipsam voluptatem quia voluptas</li>
    <li>Sed quia non numquam eius modi tempora incidunt</li>
  </ul>
  <p class="abs answers-text">Sed ut perspiciatis unde omnis iste natus error sit voluptatem accusantium do loremque laudantium, totam rem aperiam.</p>
</section>

<footer>
  <div class="abs footer"></div>
  <div class="abs footer-brand"><div class="brand-name">The<br>Copperline<br>Collective</div></div>

  <h4 class="abs f-head" style="left:340px">QUICK LINKS</h4>
  <div class="abs f-rule" style="left:340px"></div>
  <ul class="abs f-links"><li>Home</li><li>About Us</li><li>Trading</li><li>Stores</li><li>Furniture</li><li>Contact Us</li></ul>

  <h4 class="abs f-head" style="left:524px">CONTACT US</h4>
  <div class="abs f-rule" style="left:524px"></div>
  <div class="abs f-contact" style="top:2912px">
    <div class="ico"><svg viewBox="0 0 20 20" fill="#fff"><path d="M10 1a6 6 0 0 0-6 6c0 5 6 12 6 12s6-7 6-12a6 6 0 0 0-6-6zm0 8.5A2.5 2.5 0 1 1 10 4.5a2.5 2.5 0 0 1 0 5z"/></svg></div>
    <div><b>ADDRESS,</b><span>Office 1140, Northgate group</span><span>Office Tower, UK</span></div>
  </div>
  <div class="abs f-contact" style="top:2996px">
    <div class="ico"><svg viewBox="0 0 20 20" fill="none" stroke="#fff" stroke-width="2"><rect x="6" y="2" width="8" height="16" rx="1.5"/></svg></div>
    <div><b>PHONE:</b><span>180.555 0147</span></div>
  </div>
  <div class="abs f-contact" style="top:3058px">
    <div class="ico"><svg viewBox="0 0 20 20" fill="#fff"><path d="M2 5h16v10H2z"/><path d="M2 5l8 6 8-6" stroke="#15171c" stroke-width="1.5" fill="none"/></svg></div>
    <div><b>Mail:</b><span>info@copperlinecollective.com</span></div>
  </div>

  <h4 class="abs f-head" style="left:812px">CONTACT FORM</h4>
  <div class="abs f-rule" style="left:812px"></div>
  <div class="abs field" style="top:2912px;left:812px;width:140px;height:36px">Name</div>
  <div class="abs field" style="top:2912px;left:960px;width:140px;height:36px">Phone</div>
  <div class="abs field" style="top:2956px;left:812px;width:288px;height:66px">Message</div>
  <div class="abs btn-send">SEND MESSAGE</div>

  <div class="abs f-line"></div>
  <p class="abs copyright">Copyright © 2017 The Copperline Collective. All Right Reserved</p>
  <div class="abs social"><i></i>chatterbook</div>
</footer>

</body>
</html>
```